New stationary design for online film company

We need some new stationary to fit with our new logo. The stationary should be professional, clean and simple.
We need designs for a full set of business stationary.
We need - letterhead, envelopes, invoices, proposals, coverslip/note and cover page

Industry/Entity Type

Business

```html
<!DOCTYPE html>
<html lang="en">
<head>
<meta charset="utf-8">
<title>Orbitreel Stationery</title>
<link href="https://fonts.googleapis.com/css2?family=Open+Sans:wght@400;600;700&display=swap" rel="stylesheet">
<style>
  :root {
    --backdrop: #c68a5b;
    --paper: #ffffff;
    --paper-shade: #eceef2;
    --navy: #1b4a6d;
    --sky: #6aa0bb;
    --flap: #72a7c1;
    --ink: #4a4d52;
    --caption: #ffffff;
  }
  * { box-sizing: border-box; margin: 0; padding: 0; }
  html, body { width: 1200px; height: 500px; overflow: hidden; }
  body {
    position: relative;
    background: var(--backdrop);
    font-family: "Open Sans", Arial, sans-serif;
    color: var(--ink);
  }
  .sheet {
    position: absolute;
    background: linear-gradient(160deg, var(--paper) 45%, var(--paper-shade));
    overflow: hidden;
    box-shadow: 0 1px 3px rgba(0,0,0,.25);
  }
  .brand {
    position: absolute;
    display: flex;
    align-items: center;
    gap: 4px;
    font-weight: 600;
    color: var(--sky);
    letter-spacing: -0.5px;
    line-height: 1;
    white-space: nowrap;
  }
  .brand-dot {
    border-radius: 50%;
    background: var(--navy);
    flex: none;
  }
  .small { font-size: 5.5px; line-height: 1.45; color: var(--ink); white-space: nowrap; }
  .contact-line { display: flex; align-items: center; gap: 3px; }
  .icon { width: 4.5px; height: 4.5px; border-radius: 50%; background: var(--navy); flex: none; }

  /* Letterhead option 1 */
  .letterhead-one { left: 6px; top: 27px; width: 333px; height: 431px; }
  .letterhead-one .brand { left: 100px; top: 44px; font-size: 22px; }
  .letterhead-one .brand-dot { width: 22px; height: 22px; }
  .letterhead-one .footer { position: absolute; left: 39px; bottom: 7px; display: flex; gap: 6px; }

  /* Letterhead option 2 */
  .letterhead-two { left: 373px; top: 27px; width: 332px; height: 431px; }
  .letterhead-two .brand { left: 8px; top: 44px; font-size: 22px; }
  .letterhead-two .brand-dot { width: 22px; height: 22px; }
  .letterhead-two .address { position: absolute; left: 255px; top: 25px; padding-left: 4px; border-left: 0.6px solid #999; }
  .letterhead-two .contacts { position: absolute; left: 10px; top: 401px; }

  /* Envelopes */
  .envelope-back { position: absolute; left: 820px; top: 0; width: 364px; height: 180px; background: var(--paper); box-shadow: 0 1px 3px rgba(0,0,0,.25); overflow: hidden; }
  .envelope-back svg { position: absolute; left: 0; top: 0; }
  .envelope-back .brand { left: 155px; top: 32px; font-size: 13px; color: #fff; }
  .envelope-open { position: absolute; left: 738px; top: 84px; width: 372px; height: 168px; background: var(--paper); box-shadow: 0 1px 3px rgba(0,0,0,.25); overflow: hidden; }
  .envelope-open svg { position: absolute; left: 0; top: 0; }
  .envelope-open .brand { left: 158px; top: 32px; font-size: 13px; color: var(--navy); }

  .envelope-front { left: 778px; top: 158px; width: 372px; height: 168px; }
  .envelope-front .brand { left: 10px; top: 17px; font-size: 18px; }
  .envelope-front .brand-dot { width: 18px; height: 18px; }
  .envelope-front .address { position: absolute; left: 36px; top: 44px; }
  .envelope-front .web { position: absolute; left: 36px; top: 155px; font-size: 6px; letter-spacing: 1.5px; }

  /* Business cards */
  .card-front { left: 770px; top: 354px; width: 185px; height: 106px; }
  .card-front .brand { left: 6px; top: 12px; font-size: 17px; }
  .card-front .brand-dot { width: 17px; height: 17px; }
  .card-front .person { position: absolute; left: 7px; top: 50px; font-size: 6.5px; font-weight: 700; color: var(--navy); }
  .card-front .person span { font-weight: 400; font-size: 4.5px; color: var(--sky); }
  .card-front .contacts { position: absolute; left: 7px; top: 62px; font-size: 4.6px; }
  .card-front .address { position: absolute; left: 7px; top: 95px; font-size: 4.6px; }

  .card-back { left: 972px; top: 354px; width: 186px; height: 106px; }
  .card-back .brand { left: 52px; top: 48px; font-size: 19px; }
  .card-back .web { position: absolute; left: 66px; top: 89px; font-size: 5.5px; letter-spacing: 1.3px; }

  .caption { position: absolute; top: 468px; font-size: 24px; color: var(--caption); font-weight: 400; }
  .caption-one { left: 116px; }
  .caption-two { left: 482px; }
</style>
</head>
<body>

  <section class="sheet letterhead-one" aria-label="Letterhead option 1">
    <div class="brand"><span class="brand-dot"></span>orbitreel</div>
    <div class="footer small">
      <span>Street Name, City Name, State Zip Code</span>
      <span class="contact-line"><i class="icon"></i>123-456-0789</span>
      <span class="contact-line"><i class="icon"></i>info@orbitreel.com</span>
      <span class="contact-line"><i class="icon"></i>www.orbitreel.com</span>
    </div>
  </section>

  <section class="sheet letterhead-two" aria-label="Letterhead option 2">
    <div class="brand"><span class="brand-dot"></span>orbitreel</div>
    <div class="address small">Street Name, City Name<br>State Zip Code</div>
    <div class="contacts small">
      <div class="contact-line"><i class="icon"></i>123-456-0789</div>
      <div class="contact-line"><i class="icon"></i>info@orbitreel.com</div>
      <div class="contact-line"><i class="icon"></i>www.orbitreel.com</div>
    </div>
  </section>

  <section class="envelope-back" aria-label="Envelope back with coloured flap">
    <svg width="364" height="180" viewBox="0 0 364 180">
      <path d="M0 0 H364 V18 L200 70 Q182 76 164 70 L0 18 Z" fill="var(--flap)"/>
    </svg>
    <div class="brand">orbitreel</div>
  </section>

  <section class="envelope-open" aria-label="Envelope back with outlined flap">
    <svg width="372" height="168" viewBox="0 0 372 168">
      <path d="M3 1 Q10 22 40 32 L170 78 Q186 84 202 78 L335 32 Q362 22 368 1 Z" fill="#fff" stroke="#222" stroke-width="0.8"/>
    </svg>
    <div class="brand">orbitreel</div>
  </section>

  <section class="sheet envelope-front" aria-label="Envelope front">
    <div class="brand"><span class="brand-dot"></span>orbitreel</div>
    <div class="address small">Street Name, City Name, State Zip Code</div>
    <div class="web small">www.orbitreel.com</div>
  </section>

  <section class="sheet card-front" aria-label="Business card front">
    <div class="brand"><span class="brand-dot"></span>orbitreel</div>
    <div class="person">Your Name, <span>Title</span></div>
    <div class="contacts small">
      <div class="contact-line"><i class="icon"></i>123-456-0789</div>
      <div class="contact-line"><i class="icon"></i>123-456-0789</div>
      <div class="contact-line"><i class="icon"></i>info@orbitreel.com</div>
      <div class="contact-line"><i class="icon"></i>www.orbitreel.com</div>
    </div>
    <div class="address small">Street Name, City Name, State Zip Code</div>
  </section>

  <section class="sheet card-back" aria-label="Business card back">
    <div class="brand">orbitreel</div>
    <div class="web small">www.orbitreel.com</div>
  </section>

  <p class="caption caption-one">Option-1</p>
  <p class="caption caption-two">Option-2</p>

</body>
</html>
```